Envelope Design - Winner can do follow-up business

- Varnoko.com is a Swiss-based online store selling business shirts and accessories for business men
- Please visit the webpage to make yourself familiar with the company. Although the text is in German, with Plimbo translator you should be able to understand the main content.
- Our clients are mainly business men between 30 and 60 years old. Mostly with a high income working in the service industry (banking, insurance, lawyers, etc.). Sometimes there wives purchase the shirts for them ;-)
- The colors and the logo are given, as they are also used for the print materials (please see files in attachment)
- I am running several businesses and often need a talented web designer --> the winner gets substantial follow-up business
your task:
-for our company we need a new envelope design
-It should be simple and modern
-please use one of the logos in the followings.
-suprise me :)

```html
<!DOCTYPE html>
<html lang="de">
<head>
<meta charset="utf-8">
<title>Varnoko – Briefumschlag</title>
<link rel="stylesheet" href="https://fonts.googleapis.com/css2?family=Montserrat:wght@400;500;600&display=swap">
<style>
  :root {
    --backdrop: #2b2b2b;
    --paper: #f7f7f7;
    --facet-light: #fbfbfb;
    --facet-mid: #ececec;
    --facet-dark: #e2e2e2;
    --brand-gold: #e4cf63;
    --ink: #2a2a2a;
  }
  html, body {
    margin: 0;
    padding: 0;
    width: 1200px;
    height: 900px;
    overflow: hidden;
    background: var(--backdrop);
  }
  .canvas {
    position: relative;
    width: 1200px;
    height: 900px;
  }
  .envelope {
    position: absolute;
    left: 50px;
    top: 175px;
    width: 1100px;
    height: 550px;
    background: var(--paper);
    overflow: hidden;
    font-family: "Montserrat", sans-serif;
  }
  .envelope__texture {
    position: absolute;
    inset: 0;
    background: linear-gradient(135deg, var(--facet-light) 0%, var(--facet-mid) 40%, var(--facet-light) 62%, var(--facet-dark) 100%);
  }
  .brand-name {
    position: absolute;
    left: 74px;
    top: 128px;
    margin: 0;
    font-size: 54px;
    font-weight: 500;
    letter-spacing: 3px;
    line-height: 1;
    color: var(--brand-gold);
  }
  .sender {
    position: absolute;
    left: 76px;
    top: 400px;
    width: 300px;
    text-align: center;
    color: var(--ink);
    font-size: 17px;
    line-height: 22px;
    font-weight: 400;
  }
  .sender__address {
    margin: 0;
    font-style: normal;
  }
  .sender__web {
    margin: 20px 0 0;
    font-weight: 600;
  }
</style>
</head>
<body>
  <div class="canvas">
    <section class="envelope">
      <div class="envelope__texture" role="img" aria-label="Faint grey low-poly faceted background pattern"></div>
      <h1 class="brand-name">VARNOKO</h1>
      <div class="sender">
        <address class="sender__address">
          Hauptsitz/Postadresse:<br>
          Varnoko GmbH | Lindenweg 27<br>
          8716 Seldorf
        </address>
        <p class="sender__web">www.varnoko.com</p>
      </div>
    </section>
  </div>
</body>
</html>
```